Harborview Estates Business Card for Apartment Buildings

Create business cards for resident managers who run apartment buildings. The audience is the public who are searching for apartment rentals, and current residents who live at the apartment building. Key design element will be incorporating the company logo, however, the logo cannot dominate. The building name and manager name are more important than the logo. Current business card design leaves little room for copy, so we may need to reduce the size on the current card to allow for more space for copy.

Target Market(s)

Adults 18-65 years of age, who are looking for an apartment rental, plus current residents who live at our apartment buildings.

Industry/Entity Type

Property Management

Contact Information for Business Card

A major design element will be use of the company logo. Important property and manager contact information must be part of the design. The size of the logo will need to be reduced to make room for building and manager contact copy.

Font styles to use
Sans Serif

Colors
3176b5
000000
959595
ffffff

Requirements
Must have
• 1) Incorporate the company logo.
• 2) Use the company colors (dark blue, black/grey, over white).
• 3) FEATURE THE BUILDING NAME
• 4) FEATURE THE MANAGER NAME
• 5) The company name is less important than BUILDING and MANAGER
• 6) Manager contact information
• **SEE ATTACHED CREATIVE BRIEF**
Nice to have
• 1) Back of card logo watermark
• 2) Ability to write notes on back of carfd
Should not have
• Avoid letting the company logo dominate the card, the building name and manager are more important than the company logo.

```html
<!DOCTYPE html>
<html lang="en">
<head>
<meta charset="utf-8">
<title>Harborview Estates – Business Card</title>
<link rel="stylesheet" href="https://fonts.googleapis.com/css2?family=Work+Sans:wght@400;500;600;700&display=swap">
<style>
  :root {
    --blue: #1a6fb0;
    --white: #ffffff;
    --grey: #959595;
    --page: #161616;
    --card-dark: #1f1f1f;
    --card-light: #2e2e2e;
  }
  * { box-sizing: border-box; margin: 0; padding: 0; }
  html, body { width: 1200px; height: 900px; overflow: hidden; }
  body {
    background: var(--page);
    font-family: "Work Sans", Arial, sans-serif;
    color: var(--white);
    position: relative;
  }
  .card {
    position: absolute;
    left: 270px;
    width: 660px;
    height: 377px;
    background: linear-gradient(135deg, var(--card-dark) 0%, var(--card-light) 70%, var(--card-dark) 100%);
    border-radius: 3px;
    overflow: hidden;
  }
  .card--front { top: 48px; }
  .card--back { top: 475px; }

  /* Front */
  .front-brand {
    position: absolute;
    top: 140px; left: 0; right: 0;
    display: flex; align-items: center; justify-content: center; gap: 16px;
  }
  .brand-mark {
    width: 34px; height: 34px;
    background: var(--blue);
  }
  .brand-name {
    font-weight: 700;
    font-size: 34px;
    letter-spacing: 1px;
    color: var(--blue);
    text-transform: uppercase;
  }
  .front-web {
    position: absolute;
    bottom: 58px; left: 0; right: 0;
    text-align: center;
    font-size: 17px;
    letter-spacing: 2.5px;
    color: var(--white);
  }
  .front-web .accent { color: var(--blue); }

  /* Back */
  .back-brand {
    position: absolute;
    left: 40px; top: 0; bottom: 0; width: 250px;
    display: flex; flex-direction: column; align-items: center; justify-content: center; gap: 18px;
  }
  .back-brand .brand-circle {
    width: 86px; height: 86px; border-radius: 50%;
    background: var(--blue);
  }
  .back-brand .brand-name {
    font-size: 22px;
    text-align: center;
    line-height: 1.25;
  }
  .divider {
    position: absolute;
    left: 322px; top: 48px; bottom: 48px;
    width: 2px; background: var(--blue);
  }
  .details {
    position: absolute;
    left: 352px; top: 50px; right: 20px;
  }
  .manager-name {
    font-size: 24px; font-weight: 600; letter-spacing: 1px;
    color: var(--blue); text-transform: uppercase;
  }
  .manager-title { font-size: 17px; letter-spacing: 1px; margin-top: 2px; }
  .building-name {
    font-size: 16px; font-weight: 600; letter-spacing: .5px;
    color: var(--blue); text-transform: uppercase; margin-top: 14px;
  }
  .address { font-size: 16px; letter-spacing: 1px; line-height: 1.3; }
  .contact-list { list-style: none; margin-top: 14px; }
  .contact-list li {
    display: flex; align-items: center; gap: 14px;
    font-size: 16px; letter-spacing: 1px; line-height: 1.75;
  }
  .contact-list svg { width: 16px; height: 16px; fill: var(--blue); flex: none; }
  .contact-list .accent { color: var(--blue); }
</style>
</head>
<body>

  <section class="card card--front">
    <div class="front-brand">
      <span class="brand-mark"></span>
      <span class="brand-name">Harborview Estates LLC</span>
    </div>
    <p class="front-web">www.<span class="accent">harborviewest</span>.com</p>
  </section>

  <section class="card card--back">
    <div class="back-brand">
      <span class="brand-circle"></span>
      <span class="brand-name">Harborview<br>Estates LLC</span>
    </div>
    <div class="divider"></div>
    <div class="details">
      <h1 class="manager-name">Marisol Delgado</h1>
      <p class="manager-title">Resident Manager</p>
      <h2 class="building-name">Cedar Court Apartments</h2>
      <p class="address">2845 Lindell Avenue<br>San Diego, CA 92116</p>
      <ul class="contact-list">
        <li>
          <svg viewBox="0 0 16 16" aria-hidden="true"><path d="M3.5 1 6 1.5 7 5 5.3 6.3a9 9 0 0 0 4.4 4.4L11 9l3.5 1 .5 2.5-2 2C7 14 2 9 1.5 3z"/></svg>
          619-555-0142
        </li>
        <li>
          <svg viewBox="0 0 16 16" aria-hidden="true"><path d="M4 1h8v4H4zM1 6h14v6h-3v3H4v-3H1zm4 4v4h6v-4z"/></svg>
          619-555-0187
        </li>
        <li>
          <svg viewBox="0 0 16 16" aria-hidden="true"><path d="M4 0h8a1 1 0 0 1 1 1v14a1 1 0 0 1-1 1H4a1 1 0 0 1-1-1V1a1 1 0 0 1 1-1zm1 2v10h6V2zm3 11a1 1 0 1 0 0 2 1 1 0 0 0 0-2z"/></svg>
          619-555-0163
        </li>
        <li>
          <svg viewBox="0 0 16 16" aria-hidden="true"><path d="M0 3h16v1L8 9 0 4zm0 3 8 5 8-5v7H0z"/></svg>
          marisol@harborviewest.com
        </li>
        <li>
          <svg viewBox="0 0 16 16" aria-hidden="true"><path d="M8 0a8 8 0 1 0 0 16A8 8 0 0 0 8 0zm0 1.5c.9 0 2 1.9 2.3 5H5.7C6 3.4 7.1 1.5 8 1.5zM5.7 8h4.6c-.3 3.1-1.4 5-2.3 5s-2-1.9-2.3-5zM1.6 8h2.6c.1 1.9.5 3.6 1.2 4.7A6.5 6.5 0 0 1 1.6 8zm0-1.5a6.5 6.5 0 0 1 3.8-4.2C4.7 3.5 4.3 5 4.2 6.5zm10.2 0c-.1-1.5-.5-3-1.2-4.2a6.5 6.5 0 0 1 3.8 4.2zm0 1.5h2.6a6.5 6.5 0 0 1-3.8 4.7c.7-1.1 1.1-2.8 1.2-4.7z"/></svg>
          <span>www.<span class="accent">harborviewest</span>.com</span>
        </li>
      </ul>
    </div>
  </section>

</body>
</html>
```